Equipment Finance Specialist I work with companies who need the funds to buy their equipment

I would like a business card that stands out on the shelves. I want to be able to hand it to someone and say WOW. This card should have my logo.
You can put color into it I am very open on design and color

What my company does is we deal with dealerships that sell equipment such as Dump Trucks garbage trucks tractors trailers. Customers get referred to us and depending on their time in business we will ask for the following items

Companies that have been in business for more than two years we have a credit application program up to 250K . With this program we need the following items Credit application filled out(which is what I would like to be able for the customer to click on my website to get.) as well as three current month bank statements.

Deals over 250k we will need the following items

2 years business tax returns
2 years personal tax returns
Profit & Loss statement
Personal Financial Statement

what we do
100% FINANCING
SEASONAL PAYMENTS
LOAN BALLOON PAYMENTS
TRAC LEASING
LOW-INTEREST REFINANCING RATES
DEBT CONSOLIDATION

We specialize in creative financing solutions and offer a variety of reliable, flexible and expandable lending choices.

Target Market(s)

Trucking Companies

Industry/Entity Type

Trucking Company

Contact Information for Business Card

* $250,000 Application only Program
* Loans from $30,000 to 5,000,000
* Competitive Interest Rates

Font styles to use
Serif
Sans Serif

Colors

Designer to choose colors to be used in the design.

Requirements
Must have
• On the back of the card.
• * $250,000 Application only Program
• * Loans from $30,000 to 5,000,000
• My name, email, website. address
• * Competitive Interest Rates
• * 100% Financing
Nice to have
• I want my logo to pop on the card
• My logo is the great one I would like to use
Should not have
• I am up for your creativity as well

```html
<!DOCTYPE html>
<html lang="en">
<head>
<meta charset="utf-8">
<title>Ridgeline Capital – Business Card</title>
<link rel="stylesheet" href="https://fonts.googleapis.com/css2?family=Michroma&family=Roboto:wght@400;500&display=swap">
<style>
  :root {
    --navy: #1f2a6b;
    --navy-deep: #1a2360;
    --band-blue: #2a3580;
    --red: #e0232b;
    --white: #ffffff;
    --paper: #f7f7f9;
    --steel-light: #e9ebf0;
    --steel-mid: #a7adb9;
    --charcoal: #2b2d31;
    --charcoal-deep: #17181b;
    --canvas-bg: #d8d5cf;
  }
  * { box-sizing: border-box; margin: 0; padding: 0; }
  html, body { width: 900px; height: 1200px; overflow: hidden; }
  body {
    background: var(--canvas-bg);
    font-family: "Roboto", Arial, sans-serif;
    position: relative;
  }
  .card { position: absolute; left: 88px; width: 733px; overflow: hidden; }

  /* Front */
  .card-front { top: 142px; height: 428px; background: linear-gradient(135deg, var(--white), var(--paper)); }
  .brand {
    position: absolute; left: 50px; top: 70px;
    display: flex; align-items: center; gap: 14px;
  }
  .brand-dot { width: 46px; height: 46px; border-radius: 50%; background: var(--navy); }
  .brand-name {
    font-family: "Michroma", sans-serif; font-size: 22px; line-height: 1.15;
    color: var(--navy); letter-spacing: 0.5px;
  }
  .offers {
    position: absolute; right: 57px; top: 60px; list-style: none; text-align: right;
    color: var(--navy); font-size: 16px; font-weight: 500; line-height: 21px;
  }
  .offers li::after {
    content: ""; display: inline-block; width: 8px; height: 8px;
    background: var(--red); margin-left: 9px; vertical-align: 1px;
  }
  .holder { position: absolute; left: 50px; top: 236px; }
  .holder-name {
    font-family: "Michroma", sans-serif; font-weight: 400; font-size: 19px;
    color: var(--navy); letter-spacing: 0.6px; -webkit-text-stroke: 0.6px var(--navy);
  }
  .holder-role {
    font-family: "Michroma", sans-serif; font-size: 14px; color: var(--red);
    margin-top: 4px; -webkit-text-stroke: 0.3px var(--red);
  }
  .divider {
    position: absolute; left: 50px; top: 291px; width: 627px; height: 2px;
    background: linear-gradient(90deg, var(--navy) 55%, var(--red));
  }
  .contacts {
    position: absolute; left: 50px; top: 308px; list-style: none;
    color: var(--navy); font-size: 17px; line-height: 23px;
  }
  .contacts li { display: flex; align-items: center; gap: 10px; }
  .contacts svg { width: 18px; height: 16px; fill: var(--red); }
  .address {
    position: absolute; right: 56px; top: 308px; text-align: right;
    color: var(--navy); font-size: 17px; line-height: 23px; font-style: normal;
  }
  .web-band {
    position: absolute; left: 0; right: 0; height: 52px;
    background: linear-gradient(180deg, var(--band-blue), var(--navy-deep));
    display: flex; align-items: center; justify-content: center;
    font-family: "Michroma", sans-serif; font-size: 15px; color: var(--white);
    letter-spacing: 1px; -webkit-text-stroke: 0.4px var(--white);
  }
  .card-front .web-band { bottom: 0; border-top: 3px solid #c9cde0; }

  /* Back */
  .card-back { top: 630px; height: 432px; background: var(--charcoal-deep); }
  .back-top-band { position: absolute; left: 0; right: 0; top: 0; height: 45px; background: linear-gradient(180deg, var(--band-blue), var(--navy-deep)); }
  .steel-rule { position: absolute; left: 0; right: 0; height: 9px; background: linear-gradient(180deg, var(--steel-mid), var(--steel-light) 50%, var(--steel-mid)); }
  .steel-rule.top { top: 45px; }
  .steel-rule.bottom { top: 370px; }
  .back-panel {
    position: absolute; left: 0; right: 0; top: 54px; height: 316px;
    background: radial-gradient(ellipse at 50% 45%, #4a4d53, var(--charcoal) 45%, var(--charcoal-deep));
  }
  .back-brand {
    position: absolute; left: 0; right: 0; top: 54px; height: 316px;
    display: flex; align-items: center; justify-content: center; gap: 22px;
  }
  .back-brand .brand-dot { width: 70px; height: 70px; background: var(--steel-light); }
  .back-brand .brand-name { font-size: 40px; color: var(--steel-light); line-height: 1.1; }
  .card-back .web-band { top: 379px; height: 53px; }
</style>
</head>
<body>

<section class="card card-front" aria-label="Card front">
  <div class="brand">
    <span class="brand-dot"></span>
    <span class="brand-name">RIDGELINE<br>CAPITAL</span>
  </div>

  <ul class="offers">
    <li>$250,000 Application only Program</li>
    <li>Loans from $30,000 to 5,000,000</li>
    <li>Competitive Interest Rates</li>
    <li>100% Financing</li>
  </ul>

  <div class="holder">
    <p class="holder-name">MARCUS DELGADO</p>
    <p class="holder-role">CEO/FOUNDER</p>
  </div>
  <div class="divider"></div>

  <ul class="contacts">
    <li>
      <svg viewBox="0 0 24 24" aria-hidden="true"><path d="M6.6 10.8a15.1 15.1 0 0 0 6.6 6.6l2.2-2.2c.3-.3.7-.4 1-.2 1.1.4 2.3.6 3.6.6.6 0 1 .4 1 1V20c0 .6-.4 1-1 1A17 17 0 0 1 3 4c0-.6.4-1 1-1h3.5c.6 0 1 .4 1 1 0 1.3.2 2.5.6 3.6.1.3 0 .7-.2 1z"/></svg>
      351-220-418-905
    </li>
    <li>
      <svg viewBox="0 0 24 20" aria-hidden="true"><path d="M1 2h22v16H1z M1 2l11 9 11-9" fill="var(--red)"/><path d="M2 3l10 8 10-8" fill="none" stroke="#fff" stroke-width="1.6"/></svg>
      marcus@ridgelinecapital.com
    </li>
  </ul>

  <address class="address">Rua das Flores, 148<br>4050-262, Porto</address>

  <div class="web-band">WWW.RIDGELINECAPITAL.COM</div>
</section>

<section class="card card-back" aria-label="Card back">
  <div class="back-top-band"></div>
  <div class="steel-rule top"></div>
  <div class="back-panel" role="img" aria-label="Dark brushed metal texture background"></div>
  <div class="back-brand">
    <span class="brand-dot"></span>
    <span class="brand-name">RIDGELINE<br>CAPITAL</span>
  </div>
  <div class="steel-rule bottom"></div>
  <div class="web-band">WWW.RIDGELINECAPITAL.COM</div>
</section>

</body>
</html>
```